Photography and Videography - Lanternmoth Studios - New Business Card Design

Lanternmoth Studios is a photography and Videography Company started by creative couple Renny K and Lotte V and based on the Sunshine Coast in Queensland, Australia.
We're quirky, creative and innovative people and would like a business card that keeps you looking for more than just a few seconds.
Design wise we would like a black or charcoal background with a bit of a funkier design than just a boring old rectangle shape. Perhaps curved on an edge.
Ideally we would like to be able to make a collage of all of our best photos on the reverse side of the card with the company name or logo and "catch you past the lantern..." (possibly in italics) underneath it.
On the front of the business card we would like our company name -
"Lanternmoth Studios", our motto- "Bringing Ideas To Life..." (possibly in italics) and our contact information. The background should be a darker colour like black or charcoal.
We like the look of having contact company details and contact info to one side (right) and a black and white photo of Renny K and Lotte V to the other side (left).
Thank you and Good Luck!
Industry/Entity Type
Business
Contact Information for Business Card
Business Name - Lanternmoth Studios
Slogan - Bring Ideas To life
Name - Renny K | Lotte V
Description - Photography | Videography
Phone - 0438 562 917 | 0412 873 205
Email - lanternmothstudios@mailbay.com.au
Website - www.lanternmothstudios.com.au
Like us on Friendloop (symbol)
Logo styles of interest
Pictorial/Combination Logo
Look and feel

```html
<!DOCTYPE html>
<html lang="en">
<head>
<meta charset="utf-8">
<title>Lanternmoth Studios — Business Card</title>
<link rel="stylesheet" href="https://fonts.googleapis.com/css2?family=Didact+Gothic&family=Montserrat:wght@700&display=swap">
<style>
  :root {
    --backdrop: #e9e6e1;
    --card-top: #3d3d3d;
    --card-bottom: #2c2c2c;
    --cream: #ece3b4;
    --soft-grey: #c9c6bd;
    --muted-grey: #8f8c86;
    --social-square: #4a6aa8;
  }
  html, body {
    margin: 0;
    padding: 0;
    width: 1200px;
    height: 871px;
    overflow: hidden;
    background: var(--backdrop);
  }
  .canvas {
    position: relative;
    width: 1200px;
    height: 871px;
  }
  .business-card {
    position: absolute;
    left: 365px;
    top: 50px;
    width: 470px;
    height: 770px;
    box-sizing: border-box;
    padding: 58px 44px 0 44px;
    border-radius: 6px;
    background: linear-gradient(160deg, var(--card-top), var(--card-bottom));
    box-shadow: 0 10px 30px rgba(0,0,0,0.25);
    font-family: "Didact Gothic", "Century Gothic", sans-serif;
    color: var(--cream);
  }
  .business-card p { white-space: nowrap; }
  .brand {
    display: inline-block;
  }
  .brand-name {
    margin: 0;
    font-family: "Montserrat", "Century Gothic", sans-serif;
    font-weight: 700;
    font-size: 25px;
    letter-spacing: 0.5px;
    text-transform: uppercase;
    line-height: 1;
  }
  .brand-tagline {
    margin: 5px 0 0 0;
    text-align: right;
    font-size: 13px;
    letter-spacing: 3.5px;
    color: var(--soft-grey);
  }
  .partners {
    margin: 34px 0 0 0;
    font-size: 29px;
    line-height: 1.05;
  }
  .phones {
    margin: 52px 0 0 30px;
    font-size: 29px;
    letter-spacing: 2px;
    line-height: 1.1;
  }
  .web-contacts {
    margin: 72px 0 0 56px;
    font-size: 20px;
    font-style: italic;
    line-height: 1.35;
    color: var(--soft-grey);
  }
  .services {
    margin: 92px 0 0 70px;
    font-size: 25px;
  }
  .social {
    position: absolute;
    right: 48px;
    bottom: 62px;
    display: flex;
    align-items: center;
    gap: 12px;
    font-size: 24px;
    color: var(--muted-grey);
    white-space: nowrap;
  }
  .social-square {
    display: block;
    width: 20px;
    height: 20px;
  }
</style>
</head>
<body>
  <main class="canvas">
    <article class="business-card">
      <header class="brand">
        <h1 class="brand-name">Lanternmoth Studios</h1>
        <p class="brand-tagline">Light every idea up!</p>
      </header>
      <p class="partners">Renny K<br>Lotte V</p>
      <p class="phones">0438 562 917<br>0412 873 205</p>
      <p class="web-contacts">lanternmothstudios@mailbay.com.au<br>www.lanternmothstudios.com.au</p>
      <p class="services">Photography | Videography</p>
      <div class="social">
        <span>Like us on Friendloop</span>
        <svg class="social-square" viewBox="0 0 20 20" aria-hidden="true">
          <rect width="20" height="20" rx="2" fill="var(--social-square)"/>
        </svg>
      </div>
    </article>
  </main>
</body>
</html>
```